Financial Advisor Resource Firm needs business card design

Need business card design for company in Omaha NE called Meridale Circle. We provide resources to financial advisors....workshop programs, retirement analysis, and insurance planning. I would like to see designs that use grays, greens, black, and white colors. The final design should communicate 'collaboration' and be simple yet attractive to financial planning clients. I will attached our logo and another picture of a puzzle piece coming together. I would like the incorporate the puzzle picture somehow, maybe on the back somehow, with color or just the gray scale....OR, the picture be the front of the card with 'Meridale' definition on it (see upload) and then company logo, employee name, title, address on the back (see ppt uploaded). The following disclosure needs to be included somewhere- Advisory services offered through Stonebrook Assets, LLC.
Updates

I uploaded a svg and ai file of the logo

Target Market(s)

Financial planning clients and financial advisors....so pretty diverse age range of about 40-70.

Industry/Entity Type

Financial Planning

Contact Information for Business Card

Tobias L. Fenwright, MBA
Founder/President
5287 E. Larkin Road
Suite 230
Omaha, NE 68190
Phone- (402) 555-0147
Cell- (402) 555-0183
Fax- (402) 555-0129
email- tobias@meridaleplan.example
web address- www.meridaleplan.example

Colors
1b1b1b
474747
d3d3d3
ffffff
9bcb3c
abd036

Requirements
Must have
• Must include logo provided, must be 2 sided, and must have disclosure...all of these items listed in project description

```html
<!DOCTYPE html>
<html lang="en">
<head>
<meta charset="utf-8">
<title>Meridale Circle — Business Card</title>
<link href="https://fonts.googleapis.com/css2?family=Cinzel:wght@400;600&family=Arimo:wght@400&display=swap" rel="stylesheet">
<style>
  :root {
    --ink: #1b1b1b;
    --charcoal: #474747;
    --mist: #d3d3d3;
    --paper: #ffffff;
    --leaf: #9bcb3c;
    --lime: #abd036;
    --backdrop: #ececec;
  }
  * { box-sizing: border-box; margin: 0; padding: 0; }
  html, body { width: 1200px; height: 880px; overflow: hidden; background: var(--backdrop); }
  .canvas { position: relative; width: 1200px; height: 880px; }

  .card {
    position: absolute;
    width: 620px; height: 354px;
    border-radius: 20px;
    background: var(--paper);
    overflow: hidden;
    box-shadow: 0 14px 30px rgba(0,0,0,.22);
  }
  .card--cover { left: 150px; top: 46px; }
  .card--details { left: 430px; top: 476px; }

  .cover-photo {
    position: absolute; inset: 0 0 130px 0;
    background: linear-gradient(180deg, #b9b9b9 0%, #cfcfcf 45%, #ececec 80%, #ffffff 100%);
  }

  .wordmark {
    position: absolute;
    display: flex; align-items: center; gap: 12px;
    font-family: "Cinzel", serif; font-weight: 600;
    color: var(--ink);
    letter-spacing: 1px;
    white-space: nowrap;
  }
  .wordmark__dot { width: 22px; height: 22px; border-radius: 50%; background: var(--leaf); flex: none; }
  .card--cover .wordmark { left: 120px; top: 214px; font-size: 38px; }
  .card--details .wordmark { left: 150px; top: 58px; font-size: 38px; }

  .address {
    position: absolute; left: 0; right: 0; top: 278px;
    text-align: center;
    font-family: "Arimo", sans-serif; font-size: 13px; color: var(--charcoal);
    white-space: nowrap;
  }
  .disclosure {
    position: absolute; left: 0; right: 0; bottom: 22px;
    text-align: center;
    font-family: "Arimo", sans-serif; font-size: 10.5px; color: var(--charcoal);
    white-space: nowrap;
  }

  .swoosh { position: absolute; inset: 0; width: 620px; height: 354px; }
  .swoosh__green { fill: var(--leaf); }
  .swoosh__dark { fill: var(--ink); }

  .person { position: absolute; left: 44px; top: 224px; }
  .person__name {
    font-family: "Cinzel", serif; font-weight: 400;
    font-size: 19px; color: var(--paper); letter-spacing: .5px; white-space: nowrap;
  }
  .person__title { font-family: "Arimo", sans-serif; font-size: 15px; color: var(--lime); margin-top: 2px; }

  .contact-list { position: absolute; list-style: none; font-family: "Arimo", sans-serif; font-size: 13.5px; color: var(--paper); }
  .contact-list li { display: flex; align-items: center; gap: 8px; height: 20px; white-space: nowrap; }
  .contact-list--phones { left: 44px; top: 284px; }
  .contact-list--online { left: 300px; top: 284px; }
  .icon { width: 15px; height: 15px; flex: none; }
  .icon circle { fill: var(--leaf); }
  .icon path, .icon rect, .icon ellipse { fill: none; stroke: var(--ink); stroke-width: 1.3; }
</style>
</head>
<body>
<main class="canvas">

  <section class="card card--cover" aria-label="Card back">
    <div class="cover-photo" role="img" aria-label="Grayscale photo of two hands joining puzzle pieces"></div>
    <div class="wordmark"><span class="wordmark__dot"></span>Meridale Circle</div>
    <p class="address">5287 E. Larkin Road, Suite 230 · Omaha, NE 68190</p>
    <p class="disclosure">Advisory services offered through Stonebrook Assets, LLC.</p>
  </section>

  <section class="card card--details" aria-label="Card front">
    <svg class="swoosh" viewBox="0 0 620 354" aria-hidden="true">
      <path class="swoosh__green" d="M0 203 C120 153 330 133 620 126 L620 354 L0 354 Z"/>
      <path class="swoosh__dark" d="M0 215 C120 165 330 145 620 138 L620 354 L0 354 Z"/>
    </svg>

    <div class="wordmark"><span class="wordmark__dot"></span>Meridale Circle</div>

    <div class="person">
      <p class="person__name">TOBIAS L. FENWRIGHT, MBA</p>
      <p class="person__title">Founder/President</p>
    </div>

    <ul class="contact-list contact-list--phones">
      <li><svg class="icon" viewBox="0 0 16 16"><circle cx="8" cy="8" r="8"/><path d="M5 4.5 L6.5 4.5 L7 6.5 L6 7.3 Q7 9.3 8.7 10 L9.5 9 L11.5 9.5 L11.5 11 Q7 11.5 5 4.5 Z"/></svg>(402) 555-0147</li>
      <li><svg class="icon" viewBox="0 0 16 16"><circle cx="8" cy="8" r="8"/><rect x="5.5" y="3.5" width="5" height="9" rx="1"/></svg>(402) 555-0183</li>
      <li><svg class="icon" viewBox="0 0 16 16"><circle cx="8" cy="8" r="8"/><rect x="4" y="6.5" width="8" height="5" rx="1"/><path d="M5.5 6.5 V4 H10.5 V6.5"/></svg>(402) 555-0129</li>
    </ul>

    <ul class="contact-list contact-list--online">
      <li><svg class="icon" viewBox="0 0 16 16"><circle cx="8" cy="8" r="8"/><rect x="4" y="5" width="8" height="6"/><path d="M4 5 L8 8.5 L12 5"/></svg>tobias@meridaleplan.example</li>
      <li><svg class="icon" viewBox="0 0 16 16"><circle cx="8" cy="8" r="8"/><ellipse cx="8" cy="8" rx="4" ry="4"/><path d="M4 8 H12 M8 4 Q5.5 8 8 12 M8 4 Q10.5 8 8 12"/></svg>www.meridaleplan.example</li>
    </ul>
  </section>

</main>
</body>
</html>
```